Estate Planning Law Firm opening new branch in Florida

I am an experienced estate planning attorney that recently relocated to Florida. Looking for a banner Ad to place on platforms such as HomeLane, Chatterbox and Picturely to create publicity for firm and new leads.

```html
<!DOCTYPE html>
<html lang="en">
<head>
<meta charset="utf-8">
<title>Serenova Law Firm – Banner</title>
<link href="https://fonts.googleapis.com/css2?family=Lora:wght@700&family=Roboto:wght@400;500&display=swap" rel="stylesheet">
<style>
  :root {
    --navy: #2c3b4f;
    --navy-deep: #253345;
    --teal: #1a6b6e;
    --teal-soft: rgba(26, 107, 110, 0.55);
    --mist: #eef2f3;
    --ink: #2c3b4f;
    --body: #555b62;
    --white: #ffffff;
    --dots: #c9ced3;
  }
  * { margin: 0; padding: 0; box-sizing: border-box; }
  html, body { width: 1200px; height: 630px; overflow: hidden; background: var(--white); }
  .banner { position: relative; width: 1200px; height: 630px; overflow: hidden; background: var(--white); font-family: "Roboto", sans-serif; }
  .backdrop { position: absolute; inset: 0; }
  .brand { position: absolute; left: 66px; top: 36px; display: flex; align-items: center; gap: 10px; }
  .brand-square { width: 20px; height: 20px; background: var(--teal); }
  .brand-text { display: flex; flex-direction: column; align-items: center; }
  .brand-name { font-family: "Lora", serif; font-weight: 700; font-size: 24px; letter-spacing: 0.5px; color: var(--ink); line-height: 1; }
  .brand-tag { margin-top: 5px; padding-top: 3px; border-top: 1px solid var(--teal); font-size: 8px; letter-spacing: 1px; color: var(--body); }
  .headline { position: absolute; left: 66px; top: 138px; font-family: "Lora", serif; font-weight: 700; font-size: 52px; line-height: 72px; color: var(--ink); }
  .headline-rule { position: absolute; left: 68px; top: 295px; width: 130px; height: 5px; background: var(--teal); }
  .intro { position: absolute; left: 65px; top: 334px; width: 440px; font-size: 17px; line-height: 30px; color: var(--body); }
  .intro p + p { margin-top: 6px; margin-left: -2px; }
  .contacts { position: absolute; left: 64px; top: 536px; list-style: none; font-size: 14px; color: #222; }
  .contacts li { display: flex; align-items: center; gap: 6px; height: 20px; }
  .contacts li + li { margin-top: 18px; }
  .contacts a { color: var(--teal); text-decoration: none; }
  .icon { width: 13px; height: 13px; fill: var(--teal); }
</style>
</head>
<body>
<div class="banner">
  <svg class="backdrop" width="1200" height="630" viewBox="0 0 1200 630">
    <defs>
      <linearGradient id="photoTone" x1="0" y1="0" x2="1" y2="1">
        <stop offset="0" stop-color="#b9bcc0"/>
        <stop offset="0.5" stop-color="#8a9099"/>
        <stop offset="1" stop-color="#3a4659"/>
      </linearGradient>
    </defs>
    <polygon points="245,0 330,0 372,92 287,92" fill="var(--mist)"/>
    <polygon points="340,540 430,540 470,630 380,630" fill="var(--mist)"/>
    <polygon points="470,465 560,465 620,630 530,630" fill="var(--mist)"/>
    <polygon points="0,425 62,630 0,630" fill="var(--navy)"/>
    <polygon points="540,0 1200,0 1200,630 640,630" fill="url(#photoTone)" role="img" aria-label="Photo of two attorneys in business suits, the man with arms crossed"/>
    <polygon points="960,0 1060,0 1200,420 1200,630 1140,630" fill="var(--teal-soft)"/>
    <polygon points="1110,0 1200,0 1200,220" fill="var(--white)"/>
    <polygon points="1075,0 1125,0 1168,118 1120,118" fill="var(--navy)"/>
    <polygon points="1110,220 1200,220 1200,630 1170,630" fill="var(--navy)" opacity="0.7"/>
    <polygon points="418,0 540,0 670,408 548,408" fill="var(--teal)"/>
    <polygon points="635,296 690,296 760,500 705,500" fill="var(--navy-deep)" opacity="0.8"/>
    <polygon points="618,505 662,505 702,630 658,630" fill="var(--teal)"/>
    <g fill="var(--dots)">
      <circle cx="1155" cy="6" r="2.5"/><circle cx="1170" cy="14" r="2.5"/><circle cx="1186" cy="10" r="2.5"/>
      <circle cx="1162" cy="24" r="2.5"/><circle cx="1178" cy="30" r="2.5"/><circle cx="1192" cy="24" r="2.5"/>
      <circle cx="1186" cy="44" r="2.5"/><circle cx="1196" cy="56" r="2.5"/>
    </g>
  </svg>

  <div class="brand">
    <span class="brand-square"></span>
    <div class="brand-text">
      <span class="brand-name">SERENOVA</span>
      <span class="brand-tag">LAW FIRM, PLLC</span>
    </div>
  </div>

  <h1 class="headline">Welcome To<br>Serenova</h1>
  <div class="headline-rule"></div>

  <div class="intro">
    <p>Where our mission is to bring peace of mind to working families through comprehensive estate planning, wealth management, and tax planning services.</p>
    <p>From safeguarding your family's future to optimizing your financial growth, our experienced team.</p>
  </div>

  <ul class="contacts">
    <li>
      <svg class="icon" viewBox="0 0 16 16"><rect width="16" height="16" rx="3"/><path d="M5 3.5l1.6 2.4-1 1a6 6 0 0 0 3.5 3.5l1-1 2.4 1.6-.9 1.6C8 12.4 3.6 8 3.4 4.4z" fill="#fff"/></svg>
      <span>Phone Call: <a href="tel:5550142287">(555) 014-2287</a></span>
    </li>
    <li>
      <svg class="icon" viewBox="0 0 16 16"><rect y="2" width="16" height="12" rx="1.5"/><path d="M1.5 4l6.5 5 6.5-5" fill="none" stroke="#fff" stroke-width="1.4"/></svg>
      <span>Send Email: <a href="mailto:hello@serenova.law">hello@serenova.law</a></span>
    </li>
  </ul>
</div>
</body>
</html>
```